new construction company branding

branding

Can I have a banner made so I can hang it as 1) branding my jobsite 2) advertisement

Target Market(s)

Commercial

Industry/Entity Type

Construction Trade

Font styles to use
Other font styles liked:
• Cinzel bold

Colors
EB3D1F
EC4F4E
F09395
F8D3D4
FCEDEE

Requirements
Must have
• Bright colors for advertisement
Nice to have
• 36”x48” canvas
Should not have
• To busy

```html
<!DOCTYPE html>
<html lang="en">
<head>
<meta charset="utf-8">
<title>Summit Ridge – Jobsite Banner</title>
<link href="https://fonts.googleapis.com/css2?family=Montserrat:wght@500;600;800&family=Cinzel:wght@700&display=swap" rel="stylesheet">
<style>
  :root {
    --red: #e30e0e;
    --ink: #1e1e1e;
    --paper: #ffffff;
    --silver: #e4e4e4;
    --backdrop: #d0d0d0;
  }
  * { margin: 0; padding: 0; box-sizing: border-box; }
  html, body { width: 1200px; height: 720px; overflow: hidden; background: var(--backdrop); }
  .banner {
    position: absolute; left: 30px; top: 189px;
    width: 1140px; height: 342px;
    background: var(--paper);
    overflow: hidden;
    box-shadow: 0 6px 14px rgba(0,0,0,0.25);
    font-family: "Montserrat", sans-serif;
  }
  .banner-shapes { position: absolute; inset: 0; }
  .headline {
    position: absolute; left: 17px; white-space: nowrap; font-weight: 800; line-height: 1;
  }
  .headline-top { top: 16px; font-size: 75px; color: var(--red); letter-spacing: 0.5px; }
  .headline-bottom { top: 93px; font-size: 54px; color: var(--ink); }
  .trade-label {
    position: absolute; left: 17px; top: 188px;
    font-size: 25px; font-weight: 600; color: var(--ink); letter-spacing: 0.6px; white-space: nowrap;
  }
  .phone {
    position: absolute; left: 53px; top: 240px;
    font-size: 60px; font-weight: 800; color: var(--paper); line-height: 1; letter-spacing: 0.5px;
  }
  .phone-icon { position: absolute; left: 18px; top: 248px; width: 24px; height: 46px; }
  .website {
    position: absolute; left: 16px; top: 312px;
    display: flex; align-items: center; gap: 6px;
    font-size: 18px; font-weight: 600; color: var(--paper); white-space: nowrap; line-height: 1;
  }
  .website svg { width: 14px; height: 14px; }
  .brand {
    position: absolute; left: 700px; width: 420px; text-align: center;
    font-family: "Cinzel", serif; font-weight: 700; white-space: nowrap; line-height: 1;
  }
  .brand-name { top: 228px; font-size: 30px; color: var(--silver); }
  .brand-tagline { top: 274px; font-size: 23px; color: var(--red); letter-spacing: 6px; }
</style>
</head>
<body>
  <section class="banner">
    <svg class="banner-shapes" viewBox="0 0 1140 342" width="1140" height="342" aria-hidden="true">
      <polygon class="phone-band" points="0,236 560,236 492,305 0,305" fill="var(--red)"/>
      <polygon class="web-band" points="0,305 304,305 277,342 0,342" fill="var(--ink)"/>
      <path class="brand-panel" d="M1085,0 C900,10 720,130 658,342 L1140,342 L1140,0 Z" fill="var(--ink)"/>
      <line class="rule" x1="16" y1="168" x2="431" y2="168" stroke="var(--red)" stroke-width="1.5"/>
      <polygon class="rule-marker" points="212,155 256,155 234,176 190,176" fill="var(--ink)"/>
    </svg>

    <h1 class="headline headline-top">HELPING YOU</h1>
    <h2 class="headline headline-bottom">BUILD BETTER</h2>
    <p class="trade-label">GENARAL CONTRACTOR</p>

    <svg class="phone-icon" viewBox="0 0 24 46" aria-hidden="true">
      <rect x="1.5" y="1.5" width="21" height="43" rx="3" fill="none" stroke="var(--paper)" stroke-width="3"/>
      <rect x="3" y="6" width="18" height="32" fill="var(--paper)"/>
      <rect x="9" y="40" width="6" height="2" rx="1" fill="var(--paper)"/>
    </svg>
    <p class="phone">555-0148-220</p>

    <p class="website">
      <svg viewBox="0 0 16 16" aria-hidden="true">
        <circle cx="8" cy="8" r="7" fill="none" stroke="var(--paper)" stroke-width="1.4"/>
        <ellipse cx="8" cy="8" rx="3" ry="7" fill="none" stroke="var(--paper)" stroke-width="1.2"/>
        <line x1="1" y1="8" x2="15" y2="8" stroke="var(--paper)" stroke-width="1.2"/>
      </svg>
      www.srbuilds.com
    </p>

    <p class="brand brand-name">SUMMIT RIDGE LLC</p>
    <p class="brand brand-tagline">GENERAL CONTRACTOR</p>
  </section>
</body>
</html>
```